Business cards to launch an education platform

Hi,
I am looking at having new business cards designed.
I am a startup, developing a web platform for schools and university, the education world. It's an online assessment system.
I would like a card that looks classy, and that is using the colors and the font of my logo.

I have attached:
1) my logo
2) A business card that I have designed quickly so you can have all the information required in the card, but I really don't like it.
3) The font that I am using (Lato Regular) to design my web platform
4) Some screenshots of my web platform so you can have a look at the style that I have.

Target Market(s)

Major market: Education system: Schools and university
Minor markets: Business in general

Industry/Entity Type

Business

Contact Information for Business Card

Clara Fenwick
Director

M: 0437 518 902
E: clara.fenwick@amberLoomSystems.com.au

Requirements
Must have
• The colors of my logo

```html
<!DOCTYPE html>
<html lang="en">
<head>
<meta charset="utf-8">
<title>Amber Loom Systems – Business Cards</title>
<link rel="stylesheet" href="https://fonts.googleapis.com/css2?family=Open+Sans:wght@400;600&display=swap">
<style>
  :root {
    --backdrop: #d9d6d3;
    --card: #141414;
    --card-back: #111111;
    --accent: #1fa3dc;
    --accent-deep: #1a6fb0;
    --text: #e8e8e8;
    --muted: #bdbdbd;
    --rule: #d0d0d0;
  }
  * { box-sizing: border-box; margin: 0; padding: 0; }
  html, body {
    width: 1200px; height: 814px; overflow: hidden;
    background: var(--backdrop);
    font-family: "Open Sans", Arial, sans-serif;
  }
  .canvas {
    position: relative; width: 1200px; height: 814px;
  }
  .card {
    position: absolute;
    width: 530px; height: 322px;
    border-radius: 4px;
    box-shadow: 0 8px 24px rgba(0,0,0,.25);
  }
  .card--back {
    left: 50px; top: 246px;
    background: var(--card-back);
  }
  .card--front {
    left: 620px; top: 246px;
    background: var(--card);
    color: var(--text);
  }

  /* back */
  .back-brand {
    position: absolute; left: 0; right: 0; top: 120px;
    display: flex; flex-direction: column; align-items: center; gap: 14px;
  }
  .back-brand__name {
    color: var(--accent); font-size: 22px; font-weight: 400; letter-spacing: .5px;
    display: flex; align-items: center; gap: 10px;
  }
  .brand-square {
    width: 18px; height: 18px; background: var(--accent); display: inline-block;
  }
  .back-brand__web {
    color: var(--muted); font-size: 15px;
  }

  /* front */
  .holder {
    position: absolute; left: 34px; top: 118px;
  }
  .holder__name {
    color: var(--accent); font-size: 25px; font-weight: 600; line-height: 1.1;
  }
  .holder__title {
    font-size: 15px; font-weight: 600; margin-top: 4px;
  }
  .rule {
    position: absolute; left: 106px; right: 34px; top: 168px;
    height: 1px; background: var(--rule);
  }
  .contacts {
    position: absolute; left: 34px; top: 182px;
    list-style: none; font-size: 13.5px; line-height: 22px;
  }
  .contacts li { display: flex; align-items: center; gap: 9px; }
  .contacts svg { width: 12px; height: 12px; flex: none; }
  .front-brand {
    position: absolute; right: 34px; top: 74px;
    display: flex; align-items: center; gap: 10px;
    color: var(--accent); font-size: 20px; font-weight: 400; letter-spacing: .5px;
  }
</style>
</head>
<body>
<main class="canvas">
  <section class="card card--back" aria-label="Card back">
    <div class="back-brand">
      <div class="back-brand__name"><span class="brand-square"></span>Amber Loom Systems</div>
      <div class="back-brand__web">amberLoomSystems.com.au</div>
    </div>
  </section>

  <section class="card card--front" aria-label="Card front">
    <div class="front-brand"><span class="brand-square"></span>Amber Loom Systems</div>

    <div class="holder">
      <h1 class="holder__name">Clara Fenwick</h1>
      <p class="holder__title">Director</p>
    </div>
    <div class="rule"></div>

    <ul class="contacts">
      <li>
        <svg viewBox="0 0 12 12" aria-hidden="true"><rect x="3" y="0.5" width="6" height="11" rx="1.2" fill="none" stroke="#1fa3dc" stroke-width="1.2"/><circle cx="6" cy="9.5" r=".7" fill="#1fa3dc"/></svg>
        0437 518 902
      </li>
      <li>
        <svg viewBox="0 0 12 12" aria-hidden="true"><rect x="0.5" y="2" width="11" height="8" rx="1" fill="#1fa3dc"/><path d="M1 2.6 6 6.6 11 2.6" fill="none" stroke="#141414" stroke-width="1"/></svg>
        clara.fenwick@amberLoomSystems.com.au
      </li>
      <li>
        <svg viewBox="0 0 12 12" aria-hidden="true"><circle cx="6" cy="6" r="5.5" fill="#1fa3dc"/><path d="M.5 6h11M6 .5c-2.5 3-2.5 8 0 11M6 .5c2.5 3 2.5 8 0 11" fill="none" stroke="#141414" stroke-width=".8"/></svg>
        www.amberLoomSystems.com.au
      </li>
    </ul>
  </section>
</main>
</body>
</html>
```